Brightway Haus Inc. Business Card Design

Brightway Haus Inc. is in search of a great clean design for our business cards!

Looking to incorporate our full logo and watermark on side one (however, I am open to having the text and watermark separated within the design.)

On side two, I am looking to have contact information (Name, Position, Phone #, Email, Website (www.thebrightwayhaus.ca). Can have the logo and/or watermark as part of the design if applicable.

Please add tagline "Where Shine Counts" on either side 1 or 2. This tagline can be in a sans serif, serif or cursive font as long as it compliments overall design. Capitalization can be title or sentence case depending on how it fits within the design.

Get creative!! Looking for a clean, crisp, premium design! Looking for a glossy card finish with spot UV features when printed. Cards will also be printed with rounded corners. Standard dimensions (3.5 x 2).

Target Market(s)

B2B - primary clients are business owners or property management corporations. (residential jobs are few and far between)

Industry/Entity Type

Business

Contact Information for Business Card

- clean, crisp design
- double sided
- spot UV accents and glossy finish upon printing
- standard business card size (3.5 x 2) with rounded corners
- please see project description for requirements per side

Font styles to use
Sans Serif

Requirements
Must have
• - adequate bleeds with print ready files
• - cohesive design elements between side 1 & 2
• - spot UV elements (can be on both sides or just one, use your discretion)
• - colour pallet should match the logo file provided
• - incorporate tagline "where shine counts" (this tagline can be in a serif or sans serif font as long as it is complimentary to the overall design.
Nice to have
• - Premium elements with a clean design
Should not have
• - Please omit cartoon or whimsical like designs, think premium.
• - Colours should not stray from the pallet of the provided logo.

```html
<!DOCTYPE html>
<html lang="en">
<head>
<meta charset="utf-8">
<title>Brightway Haus Inc. Business Card</title>
<link rel="stylesheet" href="https://fonts.googleapis.com/css2?family=Open+Sans:wght@400;600;700&display=swap">
<style>
  :root {
    --backdrop: #463d39;
    --card: #1c1d1f;
    --card-edge: #242528;
    --teal: #2ba6a9;
    --text: #e4e6e8;
    --muted: #b9bcbf;
    --rule: #8a8d90;
  }
  * { box-sizing: border-box; margin: 0; padding: 0; }
  html, body {
    width: 1200px;
    height: 864px;
    overflow: hidden;
    background: var(--backdrop);
    font-family: "Open Sans", Arial, sans-serif;
  }
  .canvas {
    width: 1200px;
    height: 864px;
    display: flex;
    flex-direction: column;
    align-items: center;
    justify-content: center;
    gap: 44px;
  }
  .card {
    width: 665px;
    height: 380px;
    border-radius: 18px;
    background: linear-gradient(160deg, var(--card-edge), var(--card) 60%);
    box-shadow: 0 14px 30px rgba(0,0,0,0.35);
    position: relative;
    overflow: hidden;
  }
  .brand {
    display: flex;
    align-items: center;
    gap: 12px;
    color: var(--teal);
    font-weight: 700;
    text-transform: uppercase;
    letter-spacing: -0.5px;
    white-space: nowrap;
  }
  .brand-dot {
    border-radius: 50%;
    background: var(--teal);
    flex: none;
  }
  /* Side one */
  .card-front {
    display: flex;
    flex-direction: column;
    align-items: center;
    justify-content: center;
  }
  .card-front .brand { font-size: 40px; }
  .card-front .brand-dot { width: 30px; height: 30px; }
  .tagline {
    margin-top: 34px;
    display: flex;
    align-items: center;
    gap: 16px;
    color: var(--muted);
    font-size: 17px;
  }
  .tagline-rule {
    width: 120px;
    height: 1px;
  }
  .tagline-rule.left { background: linear-gradient(90deg, transparent, var(--rule)); }
  .tagline-rule.right { background: linear-gradient(90deg, var(--rule), transparent); }
  /* Side two */
  .card-back .brand {
    position: absolute;
    left: 38px;
    top: 168px;
    font-size: 23px;
    gap: 9px;
  }
  .card-back .brand-dot { width: 20px; height: 20px; }
  .divider {
    position: absolute;
    left: 378px;
    top: 70px;
    width: 2px;
    height: 240px;
    background: linear-gradient(180deg, transparent, #d8dadc 50%, transparent);
  }
  .contact {
    position: absolute;
    left: 400px;
    top: 82px;
    color: var(--text);
    font-size: 15px;
    line-height: 1.4;
  }
  .contact-name {
    color: var(--teal);
    font-weight: 700;
    font-size: 16px;
    letter-spacing: 0.3px;
  }
  .contact-role { color: var(--muted); margin-bottom: 4px; }
  .contact-list { list-style: none; margin-top: 4px; }
  .contact-list li { display: flex; align-items: center; gap: 9px; }
  .contact-list svg { width: 13px; height: 13px; flex: none; }
</style>
</head>
<body>
<main class="canvas">
  <section class="card card-front" aria-label="Card side one">
    <div class="brand"><span class="brand-dot"></span>Brightway Haus Inc.</div>
    <div class="tagline">
      <span class="tagline-rule left"></span>
      <span>Where Shine Counts</span>
      <span class="tagline-rule right"></span>
    </div>
  </section>

  <section class="card card-back" aria-label="Card side two">
    <div class="brand"><span class="brand-dot"></span>Brightway Haus Inc.</div>
    <div class="divider"></div>
    <div class="contact">
      <p class="contact-name">MARCUS ELLERY</p>
      <p class="contact-role">CEO/FOUNDER</p>
      <p>2190 Cedarline Avenue</p>
      <p>Kelowna, BC V1Y 4P2</p>
      <ul class="contact-list">
        <li>
          <svg viewBox="0 0 16 16" aria-hidden="true"><path fill="#2ba6a9" d="M3 1h3l1.5 4-2 1.3a9 9 0 0 0 4.2 4.2L11 8.5 15 10v3a2 2 0 0 1-2 2A12 12 0 0 1 1 3a2 2 0 0 1 2-2z"/></svg>
          250 555 0148
        </li>
        <li>
          <svg viewBox="0 0 16 16" aria-hidden="true"><rect x="4" y="1" width="8" height="14" rx="1.5" fill="#2ba6a9"/><rect x="5.5" y="3" width="5" height="8" fill="#1c1d1f"/></svg>
          250 555 0172
        </li>
        <li>
          <svg viewBox="0 0 16 16" aria-hidden="true"><rect x="4" y="1" width="8" height="5" fill="#2ba6a9"/><rect x="1" y="6" width="14" height="7" rx="1" fill="#2ba6a9"/><rect x="4" y="10" width="8" height="5" fill="#2ba6a9" stroke="#1c1d1f"/></svg>
          250 555 0193
        </li>
        <li>
          <svg viewBox="0 0 16 16" aria-hidden="true"><rect x="1" y="3" width="14" height="10" rx="1" fill="#2ba6a9"/><path d="M1.5 3.5 8 9l6.5-5.5" stroke="#1c1d1f" stroke-width="1.4" fill="none"/></svg>
          hello@thebrightwayhaus.ca
        </li>
        <li>
          <svg viewBox="0 0 16 16" aria-hidden="true"><circle cx="8" cy="8" r="7" fill="#2ba6a9"/><circle cx="8" cy="8" r="2.5" fill="#1c1d1f"/></svg>
          www.thebrightwayhaus.ca
        </li>
      </ul>
    </div>
  </section>
</main>
</body>
</html>
```